Wandering Rooms Stationary Set

Wandering Rooms is a bespoke interior design firm set to provide services to VIP clients with elegance and minimalism is the main theme for our stationary set. We require a full stationary set covering A4 letterhead, A4 & A3 envelopes, business cards, USB's, CDs, email signature and any other item the designer sees fit. logo is already designed and finalized, and we require the designer to use it as is without modifying the logo.

Address to be used on letterhead / business cards ...etc shall be as follows:

Phone : +971 2 518 2047
P.O. Box : 309186
Address: Block C&D, Bldg. 47, Court 12, Abu Dhabi, United Arab Emirates
Website: www.wanderingrooms-example.com

Target Market(s)

VIP Clients

Industry/Entity Type

Interior Design

Font styles to use
Other font styles liked:
• something to be unique

Colors

Designer to choose colors to be used in the design.

Requirements
Must have
• Elegant, minimalistic
Nice to have
• Simple yet elegant design having a sharp yet clean cut format
Should not have
• No additional colours, just colours that are used in the logo (silver, black or gold)

```html
<!DOCTYPE html>
<html lang="en">
<head>
<meta charset="utf-8">
<title>Wandering Rooms Stationery Set</title>
<link rel="stylesheet" href="https://fonts.googleapis.com/css2?family=Cormorant+Garamond:wght@400&family=Arimo:wght@400;700&display=swap">
<style>
  :root {
    --backdrop: #c6c6c6;
    --paper-grey: #8b8b8b;
    --paper-grey-deep: #6d6d6d;
    --paper-grey-pocket: #858585;
    --paper-white: #f3f3f3;
    --ink-dark: #3a3a3a;
    --ink-light: #ececec;
    --ghost-on-white: rgba(0,0,0,0.05);
    --ghost-on-grey: rgba(0,0,0,0.09);
    --logo-font: "Cormorant Garamond", Georgia, serif;
    --body-font: "Arimo", Arial, sans-serif;
  }
  * { margin: 0; padding: 0; box-sizing: border-box; }
  html, body { width: 1200px; height: 1048px; overflow: hidden; background: var(--backdrop); }
  .set { position: relative; width: 1200px; height: 1048px; }
  .item { position: absolute; overflow: hidden; }
  .grey { background: var(--paper-grey); }
  .white { background: var(--paper-white); }

  .wordmark { font-family: var(--logo-font); font-weight: 400; letter-spacing: 0.14em; text-transform: uppercase; white-space: nowrap; position: absolute; }
  .wordmark.dark { color: var(--ink-dark); }
  .wordmark.light { color: var(--ink-light); }
  .ghost { position: absolute; left: 0; right: 0; text-align: center; font-family: var(--logo-font); font-weight: 400; white-space: nowrap; text-transform: uppercase; letter-spacing: 0.04em; }
  .ghost.on-white { color: var(--ghost-on-white); }
  .ghost.on-grey { color: var(--ghost-on-grey); }

  .contact { position: absolute; font-family: var(--body-font); font-size: 4.4px; line-height: 1.45; color: var(--ink-dark); text-align: right; white-space: nowrap; }
  .contact p + p { margin-top: 3px; }
  .contact.left { text-align: left; }
  .contact.light { color: #d9d9d9; }

  /* letterhead */
  .letterhead { left: 122px; top: 77px; width: 293px; height: 413px; }
  .letterhead .wordmark { left: 24px; top: 26px; font-size: 10px; }
  .letterhead .contact { right: 22px; top: 21px; }
  .letterhead .ghost { top: 340px; font-size: 34px; }

  /* open envelope */
  .envelope-open { left: 460px; top: 132px; width: 286px; height: 210px; }

  /* envelope back, printed */
  .envelope-print { left: 802px; top: 132px; width: 306px; height: 154px; }
  .envelope-print .wordmark { left: 18px; top: 22px; font-size: 9px; }
  .envelope-print .contact { left: 17px; top: 130px; }
  .envelope-print .ghost { top: 62px; font-size: 36px; }

  /* envelope with flap */
  .envelope-flap { left: 803px; top: 330px; width: 307px; height: 155px; }

  /* business cards */
  .card-front { left: 459px; top: 415px; width: 129px; height: 71px; }
  .card-front .wordmark { left: 9px; top: 27px; font-size: 5px; line-height: 1.35; letter-spacing: 0.12em; white-space: normal; width: 50px; }
  .card-front .contact { left: 68px; top: 17px; font-size: 3.3px; }
  .card-front .contact strong { font-weight: 700; }
  .card-back { left: 598px; top: 414px; width: 118px; height: 66px; }
  .card-back .wordmark { left: 0; right: 0; top: 29px; text-align: center; font-size: 6.5px; }

  /* folder front */
  .folder-front { left: 98px; top: 533px; width: 319px; height: 427px; }
  .folder-front .ghost { top: 40px; font-size: 40px; }
  .folder-front .wordmark { right: 30px; bottom: 60px; font-size: 11px; }

  /* open folder */
  .folder-open { left: 464px; top: 529px; width: 641px; height: 429px; background: var(--paper-grey); }
  .folder-open svg { position: absolute; left: 0; top: 0; }
  .inner-sheet { left: 341px; top: 9px; width: 291px; height: 286px; }
  .inner-sheet .wordmark { left: 24px; top: 26px; font-size: 10px; }
  .inner-sheet .contact { right: 22px; top: 21px; }
  .pocket-mark { position: absolute; right: 26px; bottom: 32px; font-size: 8.5px; }
</style>
</head>
<body>
<main class="set">

  <section class="item white letterhead" aria-label="A4 letterhead">
    <span class="wordmark dark">Wandering Rooms</span>
    <div class="contact">
      <p>Block C&amp;D, Bldg. 47, Court 12<br>Abu Dhabi, United Arab Emirates<br>P.O. Box: 309186</p>
      <p>Tel: +971 2 518 2047<br>www.wanderingrooms-example.com</p>
    </div>
    <span class="ghost on-white">Wandering</span>
  </section>

  <section class="item grey envelope-open" aria-label="Open envelope">
    <svg width="286" height="210" viewBox="0 0 286 210">
      <rect x="0" y="0" width="286" height="56" fill="var(--paper-grey-deep)"/>
      <path d="M8 18 H278 V56 L266 68 H20 L8 56 Z" fill="var(--paper-white)"/>
      <path d="M8 56 L20 68 H266 L278 56" fill="none" stroke="#7a7a7a" stroke-width="0.6"/>
      <rect x="0" y="56" width="286" height="154" fill="var(--paper-grey)"/>
      <path d="M0 56 L20 68 H266 L286 56" fill="none" stroke="#7e7e7e" stroke-width="0.8"/>
    </svg>
  </section>

  <section class="item grey envelope-print" aria-label="Envelope, printed side">
    <span class="ghost on-grey">Wandering</span>
    <span class="wordmark light">Wandering Rooms</span>
    <div class="contact left light">
      <p>Block C&amp;D, Bldg. 47, Court 12<br>Abu Dhabi, United Arab Emirates<br>P.O. Box: 309186</p>
    </div>
  </section>

  <section class="item grey envelope-flap" aria-label="Envelope, flap side">
    <svg width="307" height="155" viewBox="0 0 307 155">
      <path d="M0 0 L46 60 H261 L307 0" fill="none" stroke="#6f6f6f" stroke-width="0.9"/>
    </svg>
  </section>

  <section class="item white card-front" aria-label="Business card, front">
    <span class="wordmark dark">Wandering<br>Rooms</span>
    <div class="contact left">
      <p><strong>NOOR HALDEN</strong><br>General Manager</p>
      <p>Block C&amp;D, Bldg. 47, Court 12<br>Abu Dhabi, United Arab Emirates<br>P.O. Box: 309186</p>
      <p>Tel: +971 2 518 2047<br>www.wanderingrooms-example.com</p>
    </div>
  </section>

  <section class="item grey card-back" aria-label="Business card, back">
    <span class="wordmark light">Wandering Rooms</span>
  </section>

  <section class="item grey folder-front" aria-label="Presentation folder, cover">
    <span class="ghost on-grey">Wandering</span>
    <span class="wordmark light">Wandering Rooms</span>
  </section>

  <section class="item folder-open" aria-label="Presentation folder, open">
    <svg width="641" height="429" viewBox="0 0 641 429">
      <path d="M0 307 H314" stroke="#7d7d7d" stroke-width="0.8"/>
      <path d="M320.5 0 V429" stroke="#7f7f7f" stroke-width="0.8"/>
    </svg>
    <div class="item white inner-sheet">
      <span class="wordmark dark">Wandering Rooms</span>
      <div class="contact">
        <p>Block C&amp;D, Bldg. 47, Court 12<br>Abu Dhabi, United Arab Emirates<br>P.O. Box: 309186</p>
        <p>Tel: +971 2 518 2047<br>www.wanderingrooms-example.com</p>
      </div>
    </div>
    <svg width="641" height="429" viewBox="0 0 641 429">
      <path d="M328 429 V305 Q330 289 346 287 H641 V429 Z" fill="var(--paper-grey-pocket)"/>
      <path d="M328 305 Q330 289 346 287 H641" fill="none" stroke="#767676" stroke-width="0.8"/>
    </svg>
    <span class="wordmark light pocket-mark">Wandering Rooms</span>
  </section>

</main>
</body>
</html>
```